Brightfern Care Alliance Flirvo Ads

We want an ad created for the gay dating app flirvo. The size is 300x250. We want the ad to be sexy, with a shirtless man. We are advertising our free HIV and PrEP services. We are open to slogans about maybe "Bringing HIV and PrEP To You"
"Free PrEP and HIV Management"
Open to ideas.

We also offer through the Cedarline Relief Fund
Copay Assistance, Insurance Premium Assistance, Free Medical Services, etc
Our website is bfcanj.org

I do want the ad to have a Book Now Button

Gay sexually active males

```html
<!DOCTYPE html>
<html lang="en">
<head>
<meta charset="utf-8">
<title>Brightfern Care Alliance – Free PrEP &amp; HIV Management</title>
<link href="https://fonts.googleapis.com/css2?family=Cinzel:wght@400;500&family=Quicksand:wght@500;600;700&display=swap" rel="stylesheet">
<style>
  :root {
    --blue: #1f8bf3;
    --indigo: #4a3fe0;
    --violet: #b33de6;
    --pink: #f24fb2;
    --coral: #ff6a4a;
    --ink: #141418;
    --slate: #2b2f38;
    --paper: #f4f4f7;
    --skin-light: #f1c3a4;
    --skin-deep: #c98462;
    --brand-grad: linear-gradient(90deg, var(--blue) 0%, var(--indigo) 30%, var(--violet) 60%, var(--pink) 80%, var(--coral) 100%);
  }
  * { box-sizing: border-box; margin: 0; padding: 0; }
  html, body { width: 1200px; height: 1034px; overflow: hidden; background: var(--paper); }
  .ad {
    position: relative; width: 1200px; height: 1034px; overflow: hidden;
    background: radial-gradient(ellipse at 40% 50%, #ffffff 0%, var(--paper) 70%);
    font-family: "Quicksand", sans-serif; color: var(--ink);
  }
  .ad-backdrop { position: absolute; inset: 0; }
  .brand {
    position: absolute; left: 40px; top: 82px; display: flex; align-items: center; gap: 16px;
  }
  .brand-dot { width: 54px; height: 54px; border-radius: 50%; background: var(--indigo); }
  .brand-name {
    font-family: "Quicksand", sans-serif; font-weight: 700; font-size: 34px;
    color: var(--indigo); line-height: 1.05; width: 300px;
  }
  .headline { position: absolute; left: 32px; top: 238px; font-family: "Cinzel", serif; }
  .headline-free {
    font-size: 178px; line-height: 1; letter-spacing: 4px; font-weight: 400;
    background: var(--brand-grad); -webkit-background-clip: text; background-clip: text; color: transparent;
  }
  .headline-services {
    font-size: 72px; line-height: 1; margin-top: -2px;
    background: var(--brand-grad); -webkit-background-clip: text; background-clip: text; color: transparent;
  }
  .headline-management { font-size: 54px; line-height: 1; margin-top: 2px; color: var(--ink); letter-spacing: 1px; }
  .fund-intro { position: absolute; left: 37px; top: 543px; font-size: 28px; font-weight: 500; }
  .fund-name {
    position: absolute; left: 36px; top: 578px; font-family: "Cinzel", serif; font-size: 37px; font-weight: 500;
    background: var(--brand-grad); -webkit-background-clip: text; background-clip: text; color: transparent;
  }
  .benefit { position: absolute; display: flex; align-items: center; gap: 10px; font-size: 28px; font-weight: 500; line-height: 1.1; }
  .benefit svg { flex: none; }
  .benefit-copay { left: 44px; top: 636px; }
  .benefit-medical { left: 298px; top: 636px; }
  .benefit-premium { left: 48px; top: 718px; }
  .cta-rule { position: absolute; top: 866px; height: 12px; }
  .cta-rule-left { left: 0; width: 170px; background: linear-gradient(90deg, var(--blue), #3a6ff0); }
  .cta-rule-mid { left: 556px; width: 240px; background: linear-gradient(90deg, var(--indigo), var(--violet), var(--pink)); }
  .cta-rule-right { left: 1108px; width: 92px; background: var(--coral); }
  .book-button { position: absolute; left: 150px; top: 818px; width: 428px; height: 88px; }
  .book-button span {
    position: absolute; inset: 0; display: flex; align-items: center; justify-content: center;
    font-family: "Cinzel", serif; font-size: 54px; color: #fff; letter-spacing: 1px;
  }
  .contact { position: absolute; top: 942px; left: 42px; display: flex; align-items: center; font-size: 33px; font-weight: 700; }
  .contact-item { display: flex; align-items: center; gap: 8px; }
  .contact-divider { width: 4px; height: 72px; margin: 0 24px 0 30px; background: linear-gradient(180deg, var(--blue), var(--violet), var(--coral)); }
</style>
</head>
<body>
<main class="ad">
  <svg class="ad-backdrop" width="1200" height="1034" viewBox="0 0 1200 1034">
    <defs>
      <linearGradient id="swoosh-cool" x1="0" y1="0" x2="1" y2="1">
        <stop offset="0" stop-color="#1f8bf3"/><stop offset="0.45" stop-color="#4a3fe0"/>
        <stop offset="0.75" stop-color="#b33de6"/><stop offset="1" stop-color="#f24fb2"/>
      </linearGradient>
      <linearGradient id="swoosh-warm" x1="0" y1="0" x2="0.6" y2="1">
        <stop offset="0" stop-color="#ff6a4a"/><stop offset="1" stop-color="#f24fb2"/>
      </linearGradient>
      <linearGradient id="photo-tone" x1="0" y1="0" x2="1" y2="1">
        <stop offset="0" stop-color="#f1c3a4"/><stop offset="0.6" stop-color="#d99a78"/><stop offset="1" stop-color="#e9e9ec"/>
      </linearGradient>
      <linearGradient id="ribbon" x1="0" y1="0" x2="1" y2="0">
        <stop offset="0" stop-color="#23262d"/><stop offset="0.5" stop-color="#3a3e48"/><stop offset="1" stop-color="#23262d"/>
      </linearGradient>
    </defs>
    <path d="M500 0 C560 160 680 260 800 400 L760 420 C640 300 470 200 450 0 Z" fill="#dcdce0"/>
    <path d="M413 0 L500 0 C540 170 680 300 800 400 L792 410 C630 330 430 220 413 0 Z" fill="url(#swoosh-cool)"/>
    <path d="M484 212 C470 420 560 600 700 640 L690 660 C560 640 450 470 484 212 Z" fill="url(#swoosh-warm)"/>
    <path d="M1010 0 L1200 0 L1200 706 L1180 706 C1210 520 1150 300 1180 160 C1190 80 1110 20 1010 0 Z" fill="#2b2f38"/>
    <rect x="662" y="22" width="500" height="1012" rx="60" fill="url(#photo-tone)" role="img" aria-label="Photo of a smiling shirtless young man in a white towel giving two thumbs up"/>
  </svg>

  <div class="brand">
    <span class="brand-dot"></span>
    <span class="brand-name">Brightfern Care Alliance</span>
  </div>

  <h1 class="headline">
    <div class="headline-free">FREE</div>
    <div class="headline-services">PrEP &amp; HIV</div>
    <div class="headline-management">MANAGEMENT</div>
  </h1>

  <p class="fund-intro">We also offer through the</p>
  <p class="fund-name">Cedarline Relief Fund</p>

  <div class="benefit benefit-copay">
    <svg width="62" height="60" viewBox="0 0 62 60" fill="none" stroke="url(#swoosh-cool)" stroke-width="3">
      <circle cx="31" cy="18" r="14" stroke="#4a3fe0"/><path d="M31 10v16M23 18h16" stroke="#f24fb2"/>
      <path d="M4 56v-12c0-5 4-8 9-8h8l10 8h20c4 0 7 3 7 6v6" stroke="#1f8bf3"/>
    </svg>
    <span>Copay<br>Assistance</span>
  </div>
  <div class="benefit benefit-medical">
    <svg width="70" height="60" viewBox="0 0 70 60" fill="none" stroke-width="3">
      <rect x="20" y="20" width="30" height="38" stroke="#4a3fe0"/>
      <rect x="4" y="30" width="16" height="28" stroke="#1f8bf3"/><rect x="50" y="30" width="16" height="28" stroke="#f24fb2"/>
      <circle cx="35" cy="12" r="9" stroke="#b33de6"/><path d="M35 30v12M29 36h12" stroke="#ff6a4a"/>
    </svg>
    <span>Free Medical<br>Services</span>
  </div>
  <div class="benefit benefit-premium">
    <svg width="58" height="60" viewBox="0 0 58 60" fill="none" stroke-width="3">
      <path d="M29 34 C10 22 14 6 24 8 C27 9 29 12 29 12 C29 12 31 9 34 8 C44 6 48 22 29 34 Z" stroke="#b33de6"/>
      <path d="M14 20h8l4-6 5 12 3-6h8" stroke="#f24fb2"/>
      <path d="M2 56l10-14h14l12 4 14-8" stroke="#1f8bf3"/>
    </svg>
    <span>Insurance Premium Assistance</span>
  </div>

  <div class="cta-rule cta-rule-left"></div>
  <div class="cta-rule cta-rule-mid"></div>
  <div class="cta-rule cta-rule-right"></div>
  <div class="book-button">
    <svg width="428" height="88" viewBox="0 0 428 88"><path d="M0 0 H428 L404 44 L428 88 H0 L24 44 Z" fill="url(#ribbon)"/></svg>
    <span>BOOK NOW</span>
  </div>

  <div class="contact">
    <div class="contact-item">
      <svg width="36" height="36" viewBox="0 0 36 36" fill="none" stroke="#141418" stroke-width="3">
        <circle cx="18" cy="18" r="15"/><ellipse cx="18" cy="18" rx="6" ry="15"/><path d="M3 18h30M6 10h24M6 26h24"/>
      </svg>
      <span>www.bfcanj.org</span>
    </div>
    <div class="contact-divider"></div>
    <div class="contact-item">
      <svg width="38" height="38" viewBox="0 0 38 38" fill="#141418">
        <path d="M9 3l7 8-4 4c2 5 6 9 11 11l4-4 8 7-5 6C18 35 3 20 3 8Z"/>
        <path d="M22 4a12 12 0 0 1 12 12M22 10a6 6 0 0 1 6 6" stroke="#141418" stroke-width="3" fill="none"/>
      </svg>
      <span>201-555-0147</span>
    </div>
  </div>
</main>
</body>
</html>
```